new signage design for budget motel - Brookfern Lodge

renaming the budget motel as Brookfern Lodge, property located on side of a hill. therefore i choose to name is Brookfern Lodge, im looking for clean, modern look in signage design,this property does not have a Logo, plan to us signage design as a logo as well. current pole sign housing is rectangle shape and will be using same housing I'll be attaching picture of the signage for better idea. looking forward to awesome creative designs.

Industry/Entity Type

Motel

Font styles to use
Serif
Sans Serif

Requirements
Should not have
• mountains , mountain(s) with snow , trees, no black color, red color, blue letters, too much green.

```html
<!DOCTYPE html>
<html lang="en">
<head>
<meta charset="UTF-8">
<title>Brookfern Lodge — Pole Sign</title>
<link rel="stylesheet" href="https://fonts.googleapis.com/css2?family=Crimson+Text:wght@700&display=swap">
<style>
  :root {
    --page-bg: #ffffff;
    --sign-bg: #f0f1f3;
    --name-green: #1f4a22;
    --ink: #3c4a45;
    --forest-deep: #4d7358;
    --forest-mid: #7f9e88;
    --forest-mist: #c9d3cf;
    --serif: "Crimson Text", Georgia, serif;
  }
  * { margin: 0; padding: 0; box-sizing: border-box; }
  html, body {
    width: 800px;
    height: 1200px;
    overflow: hidden;
    background: var(--page-bg);
  }
  .canvas {
    position: relative;
    width: 800px;
    height: 1200px;
    display: flex;
    align-items: center;
    justify-content: center;
  }
  .sign {
    position: relative;
    width: 710px;
    height: 355px;
    background: var(--sign-bg);
    box-shadow: 0 1px 5px rgba(0, 0, 0, 0.25);
    overflow: hidden;
  }
  .sign__forest {
    position: absolute;
    inset: 0;
    width: 100%;
    height: 100%;
  }
  .sign__wordmark {
    position: absolute;
    left: 34px;
    top: 50px;
    font-family: var(--serif);
    font-weight: 700;
    font-size: 80px;
    line-height: 90px;
  }
  .sign__name {
    display: block;
    color: var(--name-green);
    letter-spacing: -0.5px;
  }
  .sign__direction {
    display: flex;
    align-items: center;
    gap: 12px;
  }
  .sign__kind {
    color: var(--ink);
    letter-spacing: -0.5px;
  }
  .sign__arrow {
    width: 160px;
    height: 64px;
    margin-top: 2px;
  }
</style>
</head>
<body>
  <main class="canvas">
    <section class="sign">
      <svg class="sign__forest" viewBox="0 0 710 355" preserveAspectRatio="none" role="img" aria-label="Photograph of a misty evergreen forest rising along a hillside">
        <defs>
          <linearGradient id="forestTone" x1="0" y1="0" x2="1" y2="0">
            <stop offset="0" stop-color="var(--forest-mist)"/>
            <stop offset="0.5" stop-color="var(--forest-mid)"/>
            <stop offset="1" stop-color="var(--forest-deep)"/>
          </linearGradient>
        </defs>
        <path d="M0,310 C250,285 430,265 530,222 S665,120 710,78 L710,355 L0,355 Z" fill="url(#forestTone)"/>
      </svg>
      <h1 class="sign__wordmark">
        <span class="sign__name">BROOKFERN</span>
        <span class="sign__direction">
          <span class="sign__kind">LODGE</span>
          <svg class="sign__arrow" viewBox="0 0 160 64" aria-hidden="true">
            <polygon points="0,19 120,19 120,0 160,32 120,64 120,45 0,45" fill="var(--ink)"/>
          </svg>
        </span>
      </h1>
    </section>
  </main>
</body>
</html>
```